I have an animal hospital. I want a poster to hang in each exam room to show a picture of a normal sized heart and then an enlarged heart of a dog that was fed a grain-free diet. I want to warn people not to feed grain-free diets. Maybe at the top of the poster, "Do you feed grain-free?" and then the x-ray comparison, then the warnings of Canine Dilated Cardiomyopathy.

```html
<!DOCTYPE html>
<html lang="en">
<head>
<meta charset="utf-8">
<title>Do You Feed Grain-Free? – Exam Room Poster</title>
<link rel="stylesheet" href="https://fonts.googleapis.com/css2?family=Kaushan+Script&family=Montserrat:wght@400;600;700;800&family=Rubik+Dirt&display=swap">
<style>
  :root {
    --backdrop: #ececec;
    --paper: #fbfbfb;
    --paper-shade: #e7e7e7;
    --ink: #2a2a2a;
    --accent: #e39a17;
    --accent-text: #b07f1c;
    --body-text: #4a4a4a;
    --film-dark: #0d0d0d;
    --film-light: #8a8a8a;
  }
  * { box-sizing: border-box; margin: 0; padding: 0; }
  html, body { width: 1200px; height: 674px; overflow: hidden; background: var(--backdrop); }
  body { position: relative; font-family: "Montserrat", sans-serif; }

  .poster {
    position: absolute; left: 360px; top: 12px; width: 480px; height: 650px;
    background: var(--paper); overflow: hidden;
    box-shadow: 0 4px 18px rgba(0,0,0,.18);
  }
  .shade-circle { position: absolute; border-radius: 50%; background: var(--paper-shade); }
  .shade-circle--top { width: 250px; height: 250px; right: -50px; top: -150px; }
  .shade-circle--bottom { width: 150px; height: 150px; left: -70px; bottom: -90px; }

  .dot-grid { position: absolute; left: 28px; top: 40px; }

  .xray { position: absolute; }
  .xray__hanger { position: absolute; left: 0; top: -36px; width: 100%; height: 38px; }
  .xray__film {
    position: absolute; left: 0; top: 0; width: 100%; height: 100%;
    background: radial-gradient(ellipse at 50% 55%, var(--film-light) 0%, #4a4a4a 40%, var(--film-dark) 78%);
    border: 5px solid #fff;
  }
  .xray--normal { left: 150px; top: 60px; width: 130px; height: 140px; }
  .xray--enlarged { left: 292px; top: 88px; width: 168px; height: 208px; }
  .xray__label {
    position: absolute; left: 0; width: 100%; text-align: center;
    font-weight: 800; font-size: 10.5px; letter-spacing: .6px; color: var(--ink); white-space: nowrap;
  }
  .xray--normal .xray__label { top: 148px; }
  .xray--enlarged .xray__label { top: 216px; font-size: 11.5px; }
  .warning-icon { position: absolute; right: 8px; bottom: 10px; width: 54px; height: 48px; }

  .headline { position: absolute; left: 36px; top: 226px; width: 250px; font-size: 0; font-weight: normal; }
  .headline span { display: block; }
  .headline__lead { font-family: "Kaushan Script", cursive; color: var(--accent); font-size: 26px; line-height: 1; }
  .headline__verb { font-family: "Rubik Dirt", sans-serif; color: var(--ink); font-size: 70px; line-height: .92; letter-spacing: 1px; }
  .headline__topic { font-family: "Kaushan Script", cursive; color: var(--accent); font-size: 38px; line-height: 1.1; margin-left: 30px; }

  .symptoms { position: absolute; left: 36px; top: 372px; width: 272px; font-size: 8px; color: var(--body-text); line-height: 1.3; }
  .symptoms p { margin-bottom: 5px; }
  .symptom-columns { display: flex; gap: 24px; margin-bottom: 6px; }
  .paw-list { list-style: none; }
  .paw-list li {
    position: relative; padding-left: 15px; margin-bottom: 2px;
    font-weight: 700; color: var(--accent-text); font-size: 8.4px;
  }
  .paw-list li::before {
    content: ""; position: absolute; left: 0; top: 2px; width: 9px; height: 8px;
    background: var(--ink); border-radius: 50% 50% 45% 45%;
  }
  .paw-list--signs li { margin-bottom: 4px; }

  .dog-photo {
    position: absolute; right: 14px; top: 330px; width: 150px; height: 230px;
    background: linear-gradient(180deg, #f4f4f4 0%, #d88a45 30%, #b9652a 60%, #6a4a3a 85%, #efefef 100%);
    border-radius: 6px; opacity: .9;
  }
</style>
</head>
<body>
  <article class="poster">
    <div class="shade-circle shade-circle--top"></div>
    <div class="shade-circle shade-circle--bottom"></div>

    <svg class="dot-grid" width="110" height="56" viewBox="0 0 110 56" aria-hidden="true">
      <defs><pattern id="dots" width="16" height="12" patternUnits="userSpaceOnUse"><circle cx="4" cy="4" r="3" fill="#e39a17"/></pattern></defs>
      <rect width="110" height="56" fill="url(#dots)"/>
    </svg>

    <figure class="xray xray--normal">
      <svg class="xray__hanger" viewBox="0 0 130 38" aria-hidden="true">
        <line x1="18" y1="37" x2="65" y2="6" stroke="#888" stroke-width="1.5" stroke-dasharray="2 1.5"/>
        <line x1="112" y1="37" x2="65" y2="6" stroke="#888" stroke-width="1.5" stroke-dasharray="2 1.5"/>
        <circle cx="65" cy="6" r="4" fill="#bbb"/>
      </svg>
      <div class="xray__film" role="img" aria-label="Chest X-ray of a dog with a normal sized heart"></div>
      <figcaption class="xray__label">NORMAL HEART</figcaption>
    </figure>

    <figure class="xray xray--enlarged">
      <svg class="xray__hanger" viewBox="0 0 168 38" aria-hidden="true">
        <line x1="22" y1="37" x2="84" y2="6" stroke="#888" stroke-width="1.5" stroke-dasharray="2 1.5"/>
        <line x1="146" y1="37" x2="84" y2="6" stroke="#888" stroke-width="1.5" stroke-dasharray="2 1.5"/>
        <circle cx="84" cy="6" r="4" fill="#bbb"/>
      </svg>
      <div class="xray__film" role="img" aria-label="Chest X-ray of a dog with an enlarged heart"></div>
      <svg class="warning-icon" viewBox="0 0 62 54" aria-hidden="true">
        <path d="M31 4 L58 50 L4 50 Z" fill="none" stroke="#e39a17" stroke-width="4" stroke-linejoin="round"/>
        <rect x="28" y="18" width="6" height="18" rx="2" fill="#e39a17"/>
        <circle cx="31" cy="42" r="3.5" fill="#e39a17"/>
      </svg>
      <figcaption class="xray__label">ENLARGED HEART</figcaption>
    </figure>

    <h1 class="headline">
      <span class="headline__lead">Do you</span>
      <span class="headline__verb">FEED</span>
      <span class="headline__topic">Grain-Free?</span>
    </h1>

    <section class="symptoms">
      <p>The major symptoms of DCM include:</p>
      <div class="symptom-columns">
        <ul class="paw-list">
          <li>Lethargy</li><li>Anorexia</li><li>Labored breathing</li><li>Panting</li>
        </ul>
        <ul class="paw-list">
          <li>Coughing</li><li>Abdominal distension</li><li>Sudden collapse</li>
        </ul>
      </div>
      <p>In some cases, dogs with preclinical DCM (prior to the appearance of symptoms) may be given a questionable diagnosis if they appear to be in fine health.</p>
      <p>On the other hand, a thorough physical exam can reveal some of the subtle symptoms of DCM, such as:</p>
      <ul class="paw-list paw-list--signs">
        <li>Pulse deficits</li>
        <li>Premature heart contractions that originate in or above the ventricles</li>
        <li>Slow capillary refill time in the mucous membrane tissues (e.g., gums are slow to turn pink again after pressing on them gently), indicating poor circulation</li>
        <li>Breathing sounds muffled or crackly due to the presence of fluid in the lungs</li>
      </ul>
    </section>

    <div class="dog-photo" role="img" aria-label="Photo of a sitting ginger and white dog beside an empty food bowl"></div>
  </article>
</body>
</html>
```